Modern Business Card for Larkwell 2018

Our company assumes the best about people. We are creating an online community of entrepreneurs and business leaders who struggle with marketing their business online.

This business card should POP! We recently got a new logo and are launching a new website next month, so our business cards should make a statement that feels:
-Fresh
-Smart
-Trustworthy
-Fun

Target Market(s)

small business owners, entrepreneurs

Industry/Entity Type

Digital Marketing

Contact Information for Business Card

Dimensions: 3.5" x 2"

Font styles to use
Sans Serif

Colors
f37122
ffffff

Requirements
Must have
• We need a business card with a modern, bold design. We will use one side of the card as a lead-generation offer, so text on one side will need to fit up to 140 characters. The business card should stick to our core colors (orange, black, and white).
Nice to have
• We think a vertical "portrait" design could be interesting.
Should not have
• Should not look like a traditional business card. The round icon should stand out from a distance.

```html
<!DOCTYPE html>
<html lang="en">
<head>
<meta charset="utf-8">
<title>Larkwell Business Card</title>
<link href="https://fonts.googleapis.com/css2?family=Roboto:wght@400;500;700;900&family=Yellowtail&display=swap" rel="stylesheet">
<style>
  :root {
    --brand-orange: #f37122;
    --card-white: #f4f4f4;
    --ink: #222222;
    --ink-soft: #555555;
    --backdrop: #6e4c34;
    --rule: #3a3a3a;
    --shadow: rgba(0, 0, 0, 0.35);
  }
  * { margin: 0; padding: 0; box-sizing: border-box; }
  html, body { width: 1200px; height: 960px; overflow: hidden; }
  body {
    background: var(--backdrop);
    font-family: "Roboto", Arial, sans-serif;
    position: relative;
  }
  .card {
    position: absolute;
    width: 600px;
    height: 343px;
    border-radius: 22px;
    background: var(--card-white);
    box-shadow: 2px 4px 6px var(--shadow);
    overflow: hidden;
  }
  .card--front { left: 314px; top: 113px; }
  .card--back { left: 311px; top: 472px; }

  /* Front */
  .front-mark {
    position: absolute;
    left: 41px; top: 32px;
    display: flex; align-items: center; gap: 18px;
  }
  .front-mark__dot {
    width: 124px; height: 124px; border-radius: 50%;
    background: var(--brand-orange);
  }
  .front-mark__name {
    color: var(--brand-orange);
    font-weight: 700;
    font-size: 30px;
    letter-spacing: 1px;
  }
  .contact {
    position: absolute;
    right: 40px; top: 210px;
    text-align: right;
  }
  .contact__role {
    font-size: 15.5px; font-weight: 400; color: var(--ink);
    letter-spacing: 0.2px;
  }
  .contact__name {
    font-family: "Yellowtail", cursive;
    font-size: 40px; line-height: 1;
    color: var(--brand-orange);
    margin-top: 14px;
    text-transform: uppercase;
  }
  .contact__email {
    font-size: 15px; font-weight: 500; color: var(--ink-soft);
    margin-top: 10px;
  }

  /* Back */
  .offer-band {
    position: absolute; left: 0; top: 0;
    width: 600px; height: 218px;
    background: var(--brand-orange);
    color: #ffffff;
  }
  .brand-block {
    position: absolute;
    left: 0; width: 260px; left: 30px; top: 58px;
    text-align: center;
  }
  .brand-block__dot {
    width: 38px; height: 38px; border-radius: 50%;
    background: #ffffff; margin: 0 auto 10px;
  }
  .brand-block__name {
    font-size: 36px; font-weight: 900; letter-spacing: 1px; line-height: 1;
  }
  .brand-block__tagline {
    font-size: 11px; font-weight: 500; letter-spacing: 1px; margin-top: 6px;
  }
  .band-divider {
    position: absolute; left: 297px; top: 28px;
    width: 1px; height: 165px; background: rgba(255,255,255,0.6);
  }
  .offer {
    position: absolute; left: 323px; top: 30px; width: 265px;
  }
  .offer__headline {
    font-size: 18px; font-weight: 700; line-height: 22px;
  }
  .offer__body {
    font-size: 15px; line-height: 19px; margin-top: 4px;
  }
  .offer__url {
    font-size: 19px; font-weight: 700; margin-top: 10px; margin-left: -2px;
  }
  .note-line {
    position: absolute; left: 36px; width: 520px;
    height: 1px; background: var(--rule);
  }
  .note-line--first { top: 260px; }
  .note-line--second { top: 300px; }
</style>
</head>
<body>
  <section class="card card--front">
    <div class="front-mark">
      <div class="front-mark__dot"></div>
      <span class="front-mark__name">LARKWELL</span>
    </div>
    <div class="contact">
      <p class="contact__role">STORY MARKETING COACH</p>
      <p class="contact__name">Mara Ellison</p>
      <p class="contact__email">mara@larkwellnow.com</p>
    </div>
  </section>

  <section class="card card--back">
    <div class="offer-band">
      <div class="brand-block">
        <div class="brand-block__dot"></div>
        <p class="brand-block__name">LARKWELL</p>
        <p class="brand-block__tagline">SHARE STORIES THAT MOVE PEOPLE</p>
      </div>
      <div class="band-divider"></div>
      <div class="offer">
        <p class="offer__headline">GROW YOUR AUDIENCE.<br>EARN MORE REVENUE.<br>BUILD A BIGGER MARK.</p>
        <p class="offer__body">Get your free Larkwell<br>Launch Kit and our<br>marketing handbook today at</p>
        <p class="offer__url">Larkwellnow.com/start</p>
      </div>
    </div>
    <div class="note-line note-line--first"></div>
    <div class="note-line note-line--second"></div>
  </section>
</body>
</html>
```